I need new business cards designed

I would like to get some new designs on business cards. I will upload my logo for reference. The business cards that were designed for me a few months ago were too difficult for the print companies to work with. My company is Quillbrook.net LLC. It is an art company that sells painting and expression cards online.

```html
<!DOCTYPE html>
<html lang="en">
<head>
<meta charset="utf-8">
<title>Quillbrook.net LLC — Business Cards</title>
<link rel="stylesheet" href="https://fonts.googleapis.com/css2?family=Open+Sans:wght@400;600;700&display=swap">
<style>
  :root {
    --backdrop: #262626;
    --card: #141414;
    --cyan: #1aa3dc;
    --indigo: #3f3d8f;
    --ink: #f2f2f2;
  }
  * { box-sizing: border-box; margin: 0; padding: 0; }
  html, body {
    width: 1200px; height: 900px; overflow: hidden;
    background: var(--backdrop);
    font-family: "Open Sans", Arial, sans-serif;
  }
  .canvas { position: relative; width: 1200px; height: 900px; }
  .card {
    position: absolute; left: 285px;
    width: 630px; height: 360px;
    background: var(--card);
    border-radius: 24px;
    box-shadow: 0 14px 34px rgba(0,0,0,.55);
  }
  .card--back { top: 50px; border-bottom: 5px solid var(--cyan); }
  .card--front { top: 480px; }

  /* brand lockup: plain square + company name */
  .brand { display: flex; align-items: center; gap: 18px; }
  .brand__mark { background: var(--cyan); flex: none; }
  .brand__name { color: var(--indigo); font-weight: 400; line-height: 1; white-space: nowrap; }

  .card--back .brand { position: absolute; left: 120px; top: 144px; }
  .card--back .brand__mark { width: 72px; height: 72px; }
  .card--back .brand__name { font-size: 54px; }

  /* front side */
  .social { position: absolute; left: 36px; top: 96px; display: flex; gap: 10px; }
  .social__tile { width: 26px; height: 26px; background: var(--cyan); border-radius: 2px; }

  .card--front .brand { position: absolute; left: 40px; top: 182px; gap: 10px; }
  .card--front .brand__mark { width: 34px; height: 34px; }
  .card--front .brand__name { font-size: 27px; }

  .divider {
    position: absolute; left: 330px; top: 80px;
    width: 2px; height: 210px; background: var(--cyan);
  }
  .contact { position: absolute; left: 352px; top: 78px; color: var(--ink); }
  .contact__name {
    color: var(--cyan); font-weight: 700; font-size: 24px;
    letter-spacing: .5px; text-transform: uppercase; line-height: 1.1;
  }
  .contact__role { font-size: 14px; margin-top: 4px; }
  .contact__address { font-size: 14px; line-height: 1.55; margin-top: 10px; }
  .contact__list { list-style: none; margin-top: 12px; font-size: 14px; }
  .contact__item { display: flex; align-items: center; gap: 9px; line-height: 1.75; }
  .contact__icon { width: 14px; height: 14px; fill: var(--cyan); flex: none; }
</style>
</head>
<body>
<main class="canvas">

  <section class="card card--back" aria-label="Card back">
    <div class="brand">
      <span class="brand__mark"></span>
      <span class="brand__name">Quillbrook.net</span>
    </div>
  </section>

  <section class="card card--front" aria-label="Card front">
    <div class="social" aria-label="Social profiles">
      <span class="social__tile"></span>
      <span class="social__tile"></span>
      <span class="social__tile"></span>
    </div>

    <div class="brand">
      <span class="brand__mark"></span>
      <span class="brand__name">Quillbrook.net</span>
    </div>

    <span class="divider"></span>

    <div class="contact">
      <div class="contact__name">Miles Carter</div>
      <div class="contact__role">Managing Director</div>
      <div class="contact__address">Your address, City<br>State, Zip 1234</div>
      <ul class="contact__list">
        <li class="contact__item">
          <svg class="contact__icon" viewBox="0 0 16 16" aria-hidden="true"><path d="M3 1h3l1.5 4-2 1.3a8 8 0 0 0 4.2 4.2L11 8.5l4 1.5v3a2 2 0 0 1-2 2A12 12 0 0 1 1 3a2 2 0 0 1 2-2z"/></svg>
          123-456-7890
        </li>
        <li class="contact__item">
          <svg class="contact__icon" viewBox="0 0 16 16" aria-hidden="true"><path d="M1 3h14v10H1z M1 3l7 6 7-6" fill="none" stroke="#1aa3dc" stroke-width="1.6"/></svg>
          info@quillbrookmail.com
        </li>
        <li class="contact__item">
          <svg class="contact__icon" viewBox="0 0 16 16" aria-hidden="true"><circle cx="8" cy="8" r="6.5" fill="none" stroke="#1aa3dc" stroke-width="1.5"/><path d="M1.5 8h13M8 1.5c-3 3.5-3 9.5 0 13M8 1.5c3 3.5 3 9.5 0 13" fill="none" stroke="#1aa3dc" stroke-width="1.2"/></svg>
          www.Quillbrook.net
        </li>
      </ul>
    </div>
  </section>

</main>
</body>
</html>
```